RTavenor Business Cards & Letterhead

I have a logo but need a design for some new business cards. We are a Design-Build Firm that specializes in the design and construction of commercial projects.
the cards need to be professional. no cartoon stuff.
i would like to have the cards in AI format so I can update the card as needed. Logo is provided.
Our Address is: 4187 Marlowe Ct. Apex, North Carolina 27614

```html
<!DOCTYPE html>
<html lang="en">
<head>
<meta charset="utf-8">
<title>RTavenor Letterhead and Business Cards</title>
<link rel="stylesheet" href="https://fonts.googleapis.com/css2?family=Lato:wght@400;700&family=Open+Sans:wght@400;700&family=Parisienne&display=swap">
<style>
  :root {
    --brand-blue: #0a6eab;
    --brand-grey: #6d6e70;
    --ink: #1f1f1f;
    --paper: #ffffff;
    --backdrop: #ebe8e3;
  }
  * { margin: 0; padding: 0; box-sizing: border-box; }
  html, body { width: 1200px; height: 942px; overflow: hidden; background: var(--backdrop); }
  body { position: relative; font-family: "Lato", sans-serif; color: var(--ink); }

  .wordmark { display: flex; align-items: center; gap: 6px; color: var(--brand-grey); font-family: "Open Sans", sans-serif; font-weight: 700; letter-spacing: -0.5px; line-height: 1; }
  .wordmark__square { background: var(--brand-blue); flex: none; }

  .letterhead { position: absolute; left: 84px; top: 89px; width: 541px; height: 765px; background: var(--paper); box-shadow: 0 2px 6px rgba(0,0,0,.18); overflow: hidden; }
  .letterhead .wordmark { position: absolute; left: 28px; top: 54px; font-size: 33px; }
  .letterhead .wordmark__square { width: 24px; height: 24px; }
  .letterhead__contact { position: absolute; left: 388px; top: 37px; border-left: 1.5px solid var(--brand-blue); padding-left: 9px; font-size: 10px; line-height: 12px; }
  .letterhead__contact p + p { margin-top: 6px; }
  .contact-line { display: flex; align-items: center; gap: 3px; }
  .contact-line svg { width: 7px; height: 7px; fill: var(--brand-blue); flex: none; }

  .letter { position: absolute; left: 27px; top: 175px; width: 488px; font-size: 11px; line-height: 12.7px; }
  .letter__date { margin-bottom: 13px; }
  .letter__block { margin-bottom: 13px; }
  .letter__salutation { font-weight: 700; font-size: 13.5px; margin-bottom: 14px; }
  .letter__body p { text-align: justify; margin-bottom: 11px; }
  .letter__closing { margin-top: 22px; }
  .letter__signature { margin-top: 50px; font-family: "Parisienne", cursive; font-size: 24px; }

  .wave { position: absolute; left: 0; bottom: 0; width: 100%; display: block; }

  .card { position: absolute; left: 673px; width: 444px; height: 254px; background: var(--paper); border-radius: 22px; box-shadow: 0 2px 6px rgba(0,0,0,.18); overflow: hidden; }
  .card--front { top: 201px; }
  .card--back { top: 488px; }
  .card--front .wordmark { position: absolute; left: 0; right: 0; top: 106px; justify-content: center; font-size: 50px; gap: 8px; }
  .card--front .wordmark__square { width: 36px; height: 36px; }
  .card--back .wordmark { position: absolute; left: 33px; top: 118px; font-size: 25px; gap: 5px; }
  .card--back .wordmark__square { width: 18px; height: 18px; }
  .card__details { position: absolute; left: 258px; top: 55px; border-left: 1.5px solid var(--brand-blue); padding-left: 11px; font-family: "Open Sans", sans-serif; font-size: 12.5px; line-height: 16px; color: #333; }
  .card__name { color: var(--brand-blue); font-weight: 700; font-size: 17px; line-height: 18px; }
  .card__title { margin-bottom: 14px; }
  .card__details .contact-line svg { width: 9px; height: 9px; }
  .card__address { margin-top: 13px; }
</style>
</head>
<body>

<svg width="0" height="0" style="position:absolute">
  <symbol id="icon-phone" viewBox="0 0 24 24"><path d="M6.6 10.8a15 15 0 0 0 6.6 6.6l2.2-2.2a1 1 0 0 1 1-.25 11.4 11.4 0 0 0 3.6.57 1 1 0 0 1 1 1V20a1 1 0 0 1-1 1A17 17 0 0 1 3 4a1 1 0 0 1 1-1h3.5a1 1 0 0 1 1 1c0 1.25.2 2.45.57 3.57a1 1 0 0 1-.25 1z"/></symbol>
  <symbol id="icon-mail" viewBox="0 0 24 24"><path d="M2 5h20v14H2zm2 2v.5l8 5 8-5V7l-8 5z"/></symbol>
  <symbol id="icon-globe" viewBox="0 0 24 24"><path d="M12 2a10 10 0 1 0 0 20 10 10 0 0 0 0-20zm-1 17.9A8 8 0 0 1 4.1 11H7l2 2v1l2 2zm6.9-2.5A2 2 0 0 0 16 16h-1v-3a1 1 0 0 0-1-1H8v-2h2a1 1 0 0 0 1-1V7h2a2 2 0 0 0 2-2v-.4a8 8 0 0 1 2.9 12.8z"/></symbol>
</svg>

<article class="letterhead">
  <div class="wordmark"><span class="wordmark__square"></span>RTAVENOR</div>
  <div class="letterhead__contact">
    <p>4187 Marlowe Ct. Apex,<br>North Carolina 27614</p>
    <p>
      <span class="contact-line"><svg><use href="#icon-phone"/></svg>919 555 0147</span>
      <span class="contact-line"><svg><use href="#icon-mail"/></svg>info@rtavenor.com</span>
      <span class="contact-line"><svg><use href="#icon-globe"/></svg>www.rtavenor.com</span>
    </p>
  </div>

  <div class="letter">
    <p class="letter__date">January-03-2020</p>
    <p class="letter__block">Mr, Paul Hendry<br>President</p>
    <p class="letter__block">Northgate Holdings<br>123 Street Name, Suite# 10<br>City, State, 120023</p>
    <p class="letter__salutation">Dear Mr, Paul</p>
    <div class="letter__body">
      <p>Lorem ipsum dolor sit amet, consectetur adipiscing elit, sed do eiusmod tempor incididunt ut labore et dolore magna aliqua. Ut enim ad minim veniam, quis nostrud exercitation ullamco laboris nisi ut aliquip ex ea commodo consequat. Duis aute irure dolor in reprehenderit in voluptate velit esse cillum dolore eu fugiat nulla pariatur.</p>
      <p>Lorem ipsum dolor sit amet, consectetur adipiscing elit, sed do eiusmod tempor incididunt ut labore et dolore magna aliqua. Ut enim ad minim veniam, quis nostrud exercitation ullamco laboris nisi ut aliquip ex ea commodo consequat. Duis aute irure dolor in reprehenderit in voluptate velit esse cillum dolore eu fugiat nulla pariatur.</p>
      <p>Lorem ipsum dolor sit amet, consectetur adipiscing elit, sed do eiusmod tempor incididunt ut labore et dolore magna aliqua. Ut enim ad minim veniam, quis nostrud exercitation ullamco laboris nisi ut aliquip ex ea commodo consequat.</p>
      <p>Excepteur sint occaecat cupidatat non proident, sunt in culpa qui officia deserunt mollit anim id est laborum. re et dolore magnam aliquam quaerat voluptatem.</p>
    </div>
    <p class="letter__closing">Regards</p>
    <p class="letter__signature">Daniel Reyes</p>
  </div>

  <svg class="wave" viewBox="0 0 541 70" preserveAspectRatio="none" aria-hidden="true">
    <path d="M0 14 C 120 30, 260 12, 420 2 C 470 -1, 510 2, 541 6 L 541 8 C 500 4, 460 4, 420 8 C 260 24, 120 46, 0 30 Z" fill="var(--brand-grey)"/>
    <path d="M0 35 C 120 52, 260 30, 420 14 C 470 9, 510 10, 541 17 L 541 70 L 0 70 Z" fill="var(--brand-blue)"/>
  </svg>
</article>

<section class="card card--front">
  <div class="wordmark"><span class="wordmark__square"></span>RTAVENOR</div>
</section>

<section class="card card--back">
  <div class="wordmark"><span class="wordmark__square"></span>RTAVENOR</div>
  <div class="card__details">
    <p class="card__name">OWEN CARVER</p>
    <p class="card__title">Managing Director</p>
    <span class="contact-line"><svg><use href="#icon-phone"/></svg>919 555 0147</span>
    <span class="contact-line"><svg><use href="#icon-mail"/></svg>info@rtavenor.com</span>
    <span class="contact-line"><svg><use href="#icon-globe"/></svg>www.rtavenor.com</span>
    <p class="card__address">4187 Marlowe Ct. Apex,<br>North Carolina 27614</p>
  </div>
  <svg class="wave" viewBox="0 0 444 46" preserveAspectRatio="none" aria-hidden="true">
    <path d="M0 14 C 100 26, 220 10, 350 1 C 390 -1, 420 2, 444 6 L 444 8 C 410 4, 380 4, 350 7 C 220 20, 100 38, 0 28 Z" fill="var(--brand-grey)"/>
    <path d="M0 31 C 100 42, 220 24, 350 10 C 390 6, 420 8, 444 13 L 444 46 L 0 46 Z" fill="var(--brand-blue)"/>
  </svg>
</section>

</body>
</html>
```